Expedition Cruise Sales Website for the Polar Regions (Antarctica & Arctic)

This will be a website for selling cruises.
This site should have a homepage, a ship page, destinations, and itineraries.
I have created a file specifying each page, and it is attached.
Pages:
1. Home
2. Cruise Lines
- 2.1 Ships
3. Destinations
- 3.1 Region - 3.2 Country - 3.3 City
4. Itineraries
- 4.1 Itinerary
5. Blog / Travel Tips 6. About Us
7. Contact
Please take a look on the attached pdf
Target Market(s)
Expedition Travelers
Coding
Coded - Design and coding required
Number of Pages Required
5+ page
Font styles to use
Look and feel
Each slider illustrates characteristics of the customer's brand and the style your logo design should communicate.

```html
<!DOCTYPE html>
<html lang="en">
<head>
<meta charset="utf-8">
<title>Glacira.co — Polar Expedition Cruises</title>
<link href="https://fonts.googleapis.com/css2?family=Outfit:wght@300;400;500;600;700&family=Roboto:wght@400;500;700&display=swap" rel="stylesheet">
<style>
:root{
  --blue:#2f6db5;
  --blue-dark:#255a98;
  --ink:#1b1f30;
  --text:#3d4150;
  --muted:#6b6f7c;
  --navy:#2b2b6c;
  --navy-deep:#25255f;
  --gray:#ececef;
  --white:#ffffff;
  --star:#f28a1a;
}
*{box-sizing:border-box;margin:0;padding:0}
html,body{width:1200px;height:3558px;overflow:hidden}
body{position:relative;background:var(--white);font-family:"Outfit",sans-serif;color:var(--ink)}
.abs{position:absolute}
a{color:inherit;text-decoration:none}

/* hero */
.hero{left:0;top:0;width:1200px;height:640px;background:linear-gradient(100deg,#c9a07a 0%,#e8d2b6 30%,#f4ebdf 55%,#dfe3e4 75%,#9fb1bd 100%)}
.hero-wave{left:0;top:540px;width:1200px;height:110px}
.logo{left:144px;top:22px;width:170px;text-align:center}
.logo-mark{width:44px;height:44px;border-radius:50%;background:var(--blue);margin:0 auto 12px}
.logo-name{font-size:33px;font-weight:600;color:var(--blue);line-height:1}
.nav{left:432px;top:34px;display:flex;gap:34px;font-size:15px;color:var(--ink)}
.nav a.active{color:var(--blue)}
.welcome{left:0;width:1545px;top:212px;text-align:center;font-size:32px;font-weight:600}
.hero-title{left:0;width:1545px;top:250px;text-align:center;font-size:78px;font-weight:700;color:var(--blue);letter-spacing:1px}
.search{left:202px;top:417px;width:796px;height:106px;background:rgba(255,255,255,.78);border:1px solid #fff;border-radius:14px}
.field{position:absolute;top:24px}
.field label{display:block;font-size:11px;color:var(--text);margin:0 0 4px 6px}
.field .box{width:184px;height:36px;background:#fff;border:1px solid #cfd3da;border-radius:18px;position:relative}
.field .box::after{content:"";position:absolute;right:16px;top:16px;border:4px solid transparent;border-top-color:#222}
.field .box.date::after{border:none;width:10px;height:9px;top:13px;border:1.5px solid #555;border-radius:1px}
.explore{position:absolute;left:594px;top:44px;width:184px;height:36px;border-radius:18px;background:var(--blue);color:#fff;font-size:12px;font-weight:600;display:flex;align-items:center;justify-content:center}
.arrow{width:40px;height:40px;border-radius:50%;background:#eeeff1;display:flex;align-items:center;justify-content:center}
.arrow.white{background:#fff}

/* headings */
.section-title{left:0;width:1200px;text-align:center;font-size:41px;font-weight:700;color:var(--ink)}
.section-title span{color:var(--blue)}

/* offers */
.offer{width:427px}
.offer-img{height:251px;border-radius:22px}
.offer h3{font-size:24px;font-weight:600;margin:16px 0 0 32px;display:inline-block;padding-bottom:8px;border-bottom:2px solid var(--blue)}
.offer p{margin:12px 32px 0;font-size:15px;line-height:28px;color:var(--text)}
.offer .price{margin:6px 32px 0;font-size:25px;font-weight:600;color:var(--blue)}

/* destinations */
.dest-band{left:0;top:1280px;width:1200px;height:536px;background:linear-gradient(180deg,#eaf3fa 0%,#dfeef6 18%,#8fd5e3 42%,#5cc7d6 60%,#bfe6ec 82%,#f4f4f4 100%)}
.dest-intro{left:230px;width:740px;top:1396px;text-align:center;font-size:15px;line-height:24px;color:var(--text)}
.dest-img{top:1465px;width:292px;height:227px;border-radius:4px}
.dest-cap{top:1704px;width:292px;text-align:center;font-size:20px;font-weight:600}

/* cruise lines */
.line-card{width:442px;height:193px;background:#fff;box-shadow:0 2px 10px rgba(0,0,0,.13);border-radius:3px}
.line-img{position:absolute;left:13px;top:13px;width:152px;height:167px;border-radius:3px}
.line-body{position:absolute;left:188px;top:28px;width:245px}
.line-body h4{font-size:21px;font-weight:600}
.line-body p{font-size:12.5px;line-height:23px;color:var(--muted);margin-top:8px}
.line-body a{display:inline-block;margin-top:6px;font-size:14px;font-weight:600;color:var(--blue);text-decoration:underline}
.more-btn{left:499px;top:2415px;width:203px;height:42px;border-radius:21px;background:var(--blue);color:#fff;font-size:14px;font-weight:600;display:flex;align-items:center;justify-content:center;z-index:2}

/* testimonials */
.testi-band{left:0;top:2470px;width:1200px;height:680px;background:linear-gradient(180deg,#fff 0%,#f1f1f3 12%,#e6e7eb 35%,#e9e2e2 45%,#ebebee 62%,var(--gray) 100%)}
.testi{width:361px;height:218px;background:#fff;border-radius:6px;box-shadow:0 2px 8px rgba(0,0,0,.05)}
.testi .stars{position:absolute;left:70px;top:24px;color:var(--star);font-size:14px;letter-spacing:2px}
.testi p{position:absolute;left:70px;top:52px;width:267px;font-size:16px;line-height:24px;color:var(--text);text-align:justify}
.testi .who{position:absolute;left:70px;top:170px;font-size:20px;font-weight:600}
.testi .who small{font-size:13px;font-weight:400;color:var(--muted);margin-left:6px}
.avatar{width:124px;height:124px;border-radius:50%;border:3px solid #fff}

/* footer */
.footer-wave{left:0;top:3080px;width:1200px;height:478px}
.footer{font-family:"Roboto",sans-serif;color:#fff}
.f-head{font-size:20px;font-weight:700;line-height:28px;letter-spacing:.3px}
.news-input{left:144px;top:3312px;width:270px;height:41px;border:1px solid rgba(255,255,255,.75);font-size:12px;display:flex;align-items:center;padding-left:17px}
.socials{left:144px;top:3376px;display:flex;gap:10px}
.socials span{width:24px;height:24px;border-radius:50%;background:var(--navy-deep);border:1px solid rgba(255,255,255,.3)}
.socials span.on{background:#fff}
.contact-item{left:503px;width:240px}
.contact-item b{display:block;margin-left:43px;font-size:15px;font-weight:500}
.contact-item small{display:block;margin-left:43px;font-size:12px;margin-top:6px;opacity:.9}
.contact-item svg{position:absolute;left:0;top:0}
.qlinks{display:flex;flex-direction:column;gap:14px;font-size:15px}
.qlinks a::before{content:"»";margin-right:14px}
.copy{left:0;top:3487px;width:1200px;height:71px;border-top:1px solid rgba(255,255,255,.15);display:flex;align-items:center;justify-content:center;font-size:14px}
</style>
</head>
<body>

<!-- hero -->
<div class="abs hero" role="img" aria-label="Couple toasting on the bow of a sailing yacht at sea in warm sunset light"></div>
<svg class="abs hero-wave" viewBox="0 0 1200 110" preserveAspectRatio="none" aria-hidden="true">
  <path d="M0 40 C120 120 260 110 380 80 C520 40 560 60 700 90 C860 120 1000 40 1200 30 L1200 110 L0 110 Z" fill="#fff"/>
</svg>

<div class="abs logo">
  <div class="logo-mark"></div>
  <div class="logo-name">Glacira.co</div>
</div>
<nav class="abs nav">
  <a class="active" href="#">Home</a><a href="#">Cruise Lines</a><a href="#">Destinations</a><a href="#">Itineraries</a><a href="#">Blog</a><a href="#">About Us</a><a href="#">Contact</a>
</nav>

<div class="abs arrow" style="left:52px;top:284px"><svg width="10" height="12" viewBox="0 0 10 12"><path d="M7 1 2 6l5 5" stroke="#333" stroke-width="1.6" fill="none"/></svg></div>
<div class="abs arrow" style="left:1108px;top:284px"><svg width="10" height="12" viewBox="0 0 10 12"><path d="M3 1l5 5-5 5" stroke="#333" stroke-width="1.6" fill="none"/></svg></div>

<div class="abs welcome">Welcome To</div>
<h1 class="abs hero-title">GLACIRA.CO</h1>

<form class="abs search">
  <div class="field" style="left:16px"><label>Destination</label><div class="box"></div></div>
  <div class="field" style="left:208px"><label>Date</label><div class="box date"></div></div>
  <div class="field" style="left:400px"><label>Cruise line</label><div class="box"></div></div>
  <div class="explore">EXPLORE NOW</div>
</form>

<!-- featured offers -->
<h2 class="abs section-title" style="top:710px">FEATURED <span>OFFERS</span></h2>
<div class="abs arrow" style="left:52px;top:888px"><svg width="10" height="12" viewBox="0 0 10 12"><path d="M7 1 2 6l5 5" stroke="#333" stroke-width="1.6" fill="none"/></svg></div>
<div class="abs arrow" style="left:1108px;top:888px"><svg width="10" height="12" viewBox="0 0 10 12"><path d="M3 1l5 5-5 5" stroke="#333" stroke-width="1.6" fill="none"/></svg></div>

<article class="abs offer" style="left:152px;top:783px">
  <div class="offer-img" role="img" aria-label="Aerial view of a large cruise ship on deep blue ocean" style="background:linear-gradient(180deg,#7fb1d6 0%,#1d5fa8 30%,#0e3f8a 100%)"></div>
  <h3>Best Antarctic Cruises</h3>
  <p>Lorem ipsum dolor sit amet, consectetur adipiscing sed do eiusmod tempor incididunt ut</p>
  <div class="price">$50.00</div>
</article>
<article class="abs offer" style="left:621px;top:783px">
  <div class="offer-img" role="img" aria-label="Small expedition boat sailing on calm sea under a bright sky" style="background:linear-gradient(180deg,#a9c9e4 0%,#e3eef6 45%,#9fb9cc 65%,#4f7591 100%)"></div>
  <h3>Top Galápagos Cruises</h3>
  <p>Lorem ipsum dolor sit amet, consectetur adipiscing sed do eiusmod tempor incididunt ut</p>
  <div class="price">$50.00</div>
</article>

<!-- highlighted destinations -->
<div class="abs dest-band" role="img" aria-label="Turquoise sea and sky with clouds behind the destinations"></div>
<h2 class="abs section-title" style="top:1340px">HIGHLIGHTED <span>DESTINATIONS</span></h2>
<p class="abs dest-intro">Lorem ipsum dolor sit amet, consectetur adipiscing elit, sed do eiusmod tempor incidi dunt ut labore et dolore magna aliqua. Ut enim ad minim veniam, quis nostrud exercita</p>
<div class="abs dest-img" style="left:142px;background:linear-gradient(180deg,#e9a77a 0%,#c7835e 45%,#e7d1bd 100%)" role="img" aria-label="Suspension bridge over a beach at sunset"></div>
<div class="abs dest-img" style="left:453px;background:linear-gradient(180deg,#3c8fd1 0%,#6a9b6d 45%,#1f93b0 75%,#7a6f55 100%)" role="img" aria-label="Traveller overlooking green island bays"></div>
<div class="abs dest-img" style="left:764px;background:linear-gradient(120deg,#f6ecc8 0%,#d8cfa0 45%,#5c6b3c 100%)" role="img" aria-label="Two hikers on a coastal cliff"></div>
<div class="abs dest-cap" style="left:142px">Lorem ipsum dolor</div>
<div class="abs dest-cap" style="left:453px">Lorem ipsum dolor</div>
<div class="abs dest-cap" style="left:764px">Lorem ipsum dolor</div>
<div class="abs arrow white" style="left:51px;top:1581px"><svg width="10" height="12" viewBox="0 0 10 12"><path d="M7 1 2 6l5 5" stroke="#333" stroke-width="1.6" fill="none"/></svg></div>
<div class="abs arrow white" style="left:1108px;top:1581px"><svg width="10" height="12" viewBox="0 0 10 12"><path d="M3 1l5 5-5 5" stroke="#333" stroke-width="1.6" fill="none"/></svg></div>

<!-- testimonials background (placed before cruise lines so it sits underneath) -->
<div class="abs testi-band" role="img" aria-label="Misty sea at sunset with a distant yacht"></div>

<!-- cruise lines -->
<h2 class="abs section-title" style="top:1893px">OUR CRUISE <span>LINES</span></h2>

<div class="abs line-card" style="left:144px;top:1975px">
  <div class="line-img" role="img" aria-label="Motor yacht at golden sunset" style="background:linear-gradient(180deg,#e7b56d 0%,#b28a63 45%,#3d4a5c 100%)"></div>
  <div class="line-body"><h4>Lorem ipsum dolor sit</h4><p>Lorem ipsum dolor sit amet, consect etur adipiscing elit, sed do eiusmod tempor incidi dunt</p><a href="#">Explore Now</a></div>
</div>
<div class="abs line-card" style="left:614px;top:1975px">
  <div class="line-img" role="img" aria-label="White superyacht on dark blue water" style="background:linear-gradient(180deg,#9db3cf 0%,#5f7ea6 40%,#1c3d73 100%)"></div>
  <div class="line-body"><h4>Lorem ipsum dolor sit</h4><p>Lorem ipsum dolor sit amet, consect etur adipiscing elit, sed do eiusmod tempor incidi dunt</p><a href="#">Explore Now</a></div>
</div>
<div class="abs line-card" style="left:144px;top:2192px">
  <div class="line-img" role="img" aria-label="Passenger boat on calm sea" style="background:linear-gradient(180deg,#b9d2e6 0%,#e2ebf1 40%,#41627e 100%)"></div>
  <div class="line-body"><h4>Lorem ipsum dolor sit</h4><p>Lorem ipsum dolor sit amet, consect etur adipiscing elit, sed do eiusmod tempor incidi dunt</p><a href="#">Explore Now</a></div>
</div>
<div class="abs line-card" style="left:614px;top:2192px">
  <div class="line-img" role="img" aria-label="Speed yacht on turquoise water" style="background:linear-gradient(180deg,#8fd0e0 0%,#2d9ac0 50%,#1172a6 100%)"></div>
  <div class="line-body"><h4>Lorem ipsum dolor sit</h4><p>Lorem ipsum dolor sit amet, consect etur adipiscing elit, sed do eiusmod tempor incidi dunt</p><a href="#">Explore Now</a></div>
</div>
<a class="abs more-btn" href="#">View More Highlights</a>

<!-- testimonials -->
<h2 class="abs section-title" style="top:2696px">CUSTOMER <span>TESTIMONIALS</span></h2>

<div class="abs testi" style="left:217px;top:2765px">
  <div class="stars">★★★★★</div>
  <p>Lorem ipsum dolor sit amet, consectetur adipiscing elit, sed do eiusmod tempor incididunt ut labore et dolore magna aliqua.</p>
  <div class="who">John doe <small>Company name</small></div>
</div>
<div class="abs avatar" style="left:143px;top:2810px;background:linear-gradient(160deg,#d8d8d8,#9a8f84)" role="img" aria-label="Portrait photo of customer"></div>

<div class="abs testi" style="left:695px;top:2765px">
  <div class="stars">★★★★★</div>
  <p>Lorem ipsum dolor sit amet, consectetur adipiscing elit, sed do eiusmod tempor incididunt ut labore et dolore magna aliqua.</p>
  <div class="who">John doe <small>Company name</small></div>
</div>
<div class="abs avatar" style="left:622px;top:2810px;background:linear-gradient(160deg,#7fc0d8,#3a7fb0)" role="img" aria-label="Portrait photo of customer"></div>

<svg class="abs" style="left:56px;top:2864px" width="16" height="28" viewBox="0 0 16 28" aria-hidden="true"><path d="M13 2 3 14l10 12" stroke="#222" stroke-width="2.5" fill="none"/></svg>
<svg class="abs" style="left:1118px;top:2864px" width="16" height="28" viewBox="0 0 16 28" aria-hidden="true"><path d="M3 2l10 12L3 26" stroke="#222" stroke-width="2.5" fill="none"/></svg>

<!-- footer -->
<svg class="abs footer-wave" viewBox="0 0 1200 478" preserveAspectRatio="none" aria-hidden="true">
  <path d="M0 62 C140 110 260 30 420 20 C560 12 600 90 700 80 C800 70 800 0 900 8 C1000 16 1080 120 1200 110 L1200 478 L0 478 Z" fill="#2b2b6c"/>
</svg>

<footer class="footer">
  <div class="abs f-head" style="left:144px;top:3250px">SUBSCRIBE TO<br>OUR NEWSLETTER</div>
  <div class="abs news-input">Email address
    <svg style="position:absolute;right:10px;top:13px" width="15" height="14" viewBox="0 0 15 14" aria-hidden="true"><path d="M1 7 14 1 10 13 7 8Z" fill="#fff"/></svg>
  </div>
  <div class="abs socials"><span></span><span class="on"></span><span></span><span></span></div>

  <div class="abs f-head" style="left:503px;top:3250px">CONTACT INFO</div>
  <div class="abs contact-item" style="top:3298px">
    <svg width="14" height="18" viewBox="0 0 14 18" aria-hidden="true"><path d="M7 0a7 7 0 0 0-7 7c0 5 7 11 7 11s7-6 7-11a7 7 0 0 0-7-7zm0 10a3 3 0 1 1 0-6 3 3 0 0 1 0 6z" fill="#fff"/></svg>
    <b>Address</b><small>Lorem ipsum dolor sit amet</small>
  </div>
  <div class="abs contact-item" style="top:3354px">
    <svg width="20" height="14" viewBox="0 0 20 14" aria-hidden="true"><rect width="20" height="14" rx="1" fill="#fff"/><path d="M1 1l9 7 9-7" stroke="#2b2b6c" stroke-width="1.5" fill="none"/></svg>
    <b>Email</b><small>info@companyname.com</small>
  </div>
  <div class="abs contact-item" style="top:3410px">
    <svg width="17" height="17" viewBox="0 0 17 17" aria-hidden="true"><path d="M3.5 1 6 4.5 4.5 6.5c1 2.3 3.2 4.5 5.5 5.5l2-1.5L15.5 13l-1.5 3C7 16 1 10 1 3z" fill="#fff"/></svg>
    <b>Phone</b><small>+1 888 888 8888</small>
  </div>

  <div class="abs f-head" style="left:765px;top:3250px">QUICK LINKS</div>
  <div class="abs qlinks" style="left:765px;top:3298px"><a href="#">Home</a><a href="#">About</a><a href="#">Services</a><a href="#">Contact</a></div>
  <div class="abs qlinks" style="left:900px;top:3298px"><a href="#">Terms and Condition</a><a href="#">Privacy policy</a><a href="#">Help</a><a href="#">Faq</a></div>

  <div class="abs copy">© Copyrights 2025 | All Rights Reserved</div>
</footer>

</body>
</html>
```